Web Site Design and Business Card design for Recruiting Company

There are three major tasks in this project:
1) I need to re-design my newly created website www.talvoro.net using the same logo but creating a totally different recruiting template that will apply better for a recruitment site. I want to use the elements of the Talvoro Network logo (which is the road junction) and red, black and gray colors throughout the website. I need someone to both design and launch the site...
2) I would also like to design a double sided business card using the same logo/colors and elements as described above
3) I would also like to have a small thumbnail logo created. As our large logo cannot be previewed easily on the Pelmwork or on Google Chrome tab images

The design should be contemporary, minimalist and slick

```html
<!DOCTYPE html>
<html lang="en">
<head>
<meta charset="utf-8">
<title>Talvoro Network</title>
<link href="https://fonts.googleapis.com/css2?family=Montserrat:wght@400;500;600;700&family=Open+Sans:wght@400;600;700&display=swap" rel="stylesheet">
<style>
:root{
  --red:#e3151c;
  --red-dark:#b70f15;
  --black:#111111;
  --ink:#222222;
  --grey:#777777;
  --light:#f4f4f4;
  --line:#e3e3e3;
  --white:#ffffff;
}
*{margin:0;padding:0;box-sizing:border-box}
html,body{width:1200px;height:5132px;overflow:hidden}
body{font-family:"Open Sans",Arial,sans-serif;color:var(--ink);background:var(--white);font-size:13px;position:relative}
h1,h2,h3,h4,.nav,.btn{font-family:"Montserrat",Arial,sans-serif}
.abs{position:absolute}
.btn{display:inline-block;background:var(--red);color:var(--white);font-size:12px;font-weight:600;text-transform:uppercase;padding:12px 30px;border-radius:3px;letter-spacing:.5px}

/* top bar */
.topbar{top:0;left:0;width:1200px;height:40px;background:var(--black);color:#ddd;font-size:12px;display:flex;align-items:center;padding:0 120px}
.topbar .contact{display:flex;gap:28px}
.topbar .contact span{display:flex;align-items:center;gap:6px}
.topbar .social{margin-left:auto;display:flex;gap:6px}
.dot{width:18px;height:18px;border-radius:50%;background:var(--red);display:block}

/* header */
.header{top:40px;left:0;width:1200px;height:100px;background:var(--white);display:flex;align-items:center;padding:0 120px;box-shadow:0 2px 6px rgba(0,0,0,.08);z-index:2}
.brand{display:flex;align-items:center;gap:10px;font-family:"Montserrat",sans-serif;font-weight:700;font-size:20px;color:var(--ink)}
.brand i{width:18px;height:18px;background:var(--red);display:block}
.nav{margin-left:auto;display:flex;gap:34px;font-size:14px;font-weight:600}
.nav a{color:var(--ink);text-decoration:none}
.nav a.active{color:var(--red)}

/* hero */
.hero{top:140px;left:0;width:1200px;height:628px;background:linear-gradient(135deg,#3a3a3a,#6b6460 45%,#2b2b2b);color:var(--white);text-align:center}
.hero-shade{position:absolute;inset:0;background:rgba(0,0,0,.45)}
.hero h1{position:absolute;top:128px;width:100%;font-size:36px;font-weight:700;letter-spacing:1px}
.hero .sub{position:absolute;top:180px;width:100%;font-size:14px;color:#eee}
.search{position:absolute;top:256px;left:140px;width:920px;height:56px;display:flex;gap:8px}
.search .field{flex:1;background:var(--white);border-radius:3px;color:#888;font-size:13px;text-align:left;padding:0 16px;display:flex;align-items:center}
.search .go{width:150px;background:var(--red);border-radius:3px;font-family:"Montserrat",sans-serif;font-weight:700;display:flex;align-items:center;justify-content:center}
.trending{position:absolute;top:340px;left:140px;width:920px;display:flex;gap:52px;font-size:12px;color:#ddd}
.trending b{color:var(--white)}
.trending .adv{margin-left:auto;display:flex;align-items:center;gap:6px}
.cats{position:absolute;top:440px;left:120px;width:960px;display:flex;justify-content:space-between}
.cat{width:150px;display:flex;flex-direction:column;align-items:center;gap:14px;font-size:13px}
.cat svg{width:52px;height:52px}

/* jobs */
.section-title{width:100%;text-align:center;font-size:32px;font-weight:600;color:var(--ink)}
.section-sub{width:100%;text-align:center;font-size:13px;color:var(--grey)}
.tabs{top:990px;left:0;width:1200px;display:flex;justify-content:center;gap:14px}
.tab{padding:14px 26px;font-family:"Montserrat",sans-serif;font-size:12px;font-weight:600;color:var(--white);background:var(--black);border-radius:3px;text-transform:uppercase}
.tab.on{background:var(--red)}
.jobs{top:1068px;left:112px;width:976px;display:grid;grid-template-columns:1fr 1fr;column-gap:24px;row-gap:36px}
.job{position:relative;height:136px;border:1px solid var(--line);border-radius:3px;box-shadow:0 2px 8px rgba(0,0,0,.06);display:flex;align-items:center;padding:0 22px}
.job .flag{position:absolute;top:-1px;left:-1px;width:26px;height:26px;background:var(--red);clip-path:polygon(0 0,100% 0,0 100%)}
.job .co{width:110px;font-family:"Montserrat",sans-serif;font-weight:700;font-size:15px;color:var(--red)}
.job .info{flex:1}
.job .info h4{font-size:14px;font-weight:600;margin-bottom:8px}
.job .info p{font-size:11px;color:var(--grey);display:flex;align-items:center;gap:8px;margin-top:4px}
.job .info p i{width:8px;height:8px;border-radius:50%;background:var(--red);display:block}
.job .type{background:#cfcfcf;color:var(--white);font-size:11px;padding:8px 14px;border-radius:2px;margin-right:14px}
.job .heart{width:20px;height:20px}

/* companies */
.companies{top:1780px;left:0;width:1200px;height:800px;background:linear-gradient(180deg,#1c1c1c,#2e2e2e);color:var(--white);text-align:center}
.companies .label{position:absolute;top:92px;width:100%;font-size:12px;font-weight:600;letter-spacing:1px}
.companies h2{position:absolute;top:120px;left:280px;width:640px;font-size:30px;font-weight:500;line-height:1.3}
.co-cards{position:absolute;top:236px;left:108px;width:984px;display:flex;gap:24px}
.co-card{flex:1;background:var(--white);color:var(--ink);border-radius:3px;overflow:hidden;position:relative;height:464px}
.co-card .photo{height:240px;background:linear-gradient(135deg,#d9d4cf,#8a8580)}
.co-card .badge{position:absolute;top:204px;left:50%;margin-left:-36px;width:72px;height:72px;border-radius:50%;background:var(--white);box-shadow:0 2px 6px rgba(0,0,0,.15)}
.co-card .badge.red{background:var(--red)}
.co-card h3{margin-top:56px;font-size:20px;font-weight:500}
.stars{color:#f4b400;font-size:16px;letter-spacing:2px;margin-top:8px}
.co-card .meta{font-size:11px;color:var(--grey);margin-top:14px}
.pager{position:absolute;top:746px;width:100%;display:flex;justify-content:center;gap:8px}
.pager i{width:8px;height:8px;border-radius:50%;background:var(--white);display:block}

/* special */
.features{top:2740px;left:120px;width:960px;display:flex;gap:40px}
.feature{flex:1;border:1px solid var(--line);padding:26px 24px;box-shadow:0 2px 8px rgba(0,0,0,.05);height:200px}
.feature h4{display:flex;align-items:center;gap:12px;font-size:14px;font-weight:600;margin-bottom:16px}
.feature h4 i{width:28px;height:28px;border:2px solid var(--red);border-radius:4px;display:block}
.feature p{font-size:12px;color:var(--grey);line-height:1.7}
.feature .more{margin-top:14px;font-size:11px;font-weight:700;color:var(--red)}
.quote{top:3060px;left:180px;width:840px;text-align:center;font-size:14px;color:#555;line-height:1.8}
.avatars{top:3180px;left:0;width:1200px;display:flex;justify-content:center;align-items:center;gap:26px}
.avatar{width:70px;height:70px;border-radius:50%;background:linear-gradient(135deg,#c9c1ba,#8b827c)}
.avatar.big{width:100px;height:100px}

/* stats */
.stats{top:3448px;left:0;width:1200px;height:432px;background:linear-gradient(135deg,var(--red),var(--red-dark));color:var(--white);display:flex;justify-content:center;gap:60px;padding-top:72px}
.stat{width:180px;text-align:center}
.stat .ring{width:120px;height:120px;margin:0 auto;border-radius:50%;border:3px solid rgba(255,255,255,.6);display:flex;align-items:center;justify-content:center}
.stat .ring svg{width:46px;height:46px}
.stat b{display:block;font-family:"Montserrat",sans-serif;font-size:32px;margin-top:34px}
.stat span{font-size:11px;text-transform:uppercase;letter-spacing:.5px}

/* candidates */
.grid{top:4060px;left:160px;width:880px;display:grid;grid-template-columns:repeat(4,1fr)}
.cand{height:240px;border-right:1px solid var(--line);border-bottom:1px solid var(--line);display:flex;flex-direction:column;align-items:center;justify-content:center}
.cand:nth-child(4n){border-right:none}
.cand:nth-child(n+5){border-bottom:none}
.cand .pic{width:100px;height:100px;border-radius:50%;background:linear-gradient(135deg,#d3cbc4,#8f8680);margin-bottom:18px}
.cand h4{font-size:14px;font-weight:600}
.cand span{font-size:11px;color:var(--grey);margin-top:4px}

/* footer */
.footer{top:4724px;left:0;width:1200px;height:408px;background:var(--black);color:#bbb}
.footer .about{position:absolute;top:72px;left:110px;width:300px;font-size:12px;line-height:1.8}
.footer .outline{display:inline-block;margin-top:18px;border:1px solid #888;color:var(--white);font-size:11px;padding:8px 18px;border-radius:3px}
.footer .fsocial{display:flex;gap:8px;margin-top:26px}
.footer .fsocial i{width:26px;height:26px;border:1px solid #888;border-radius:50%;display:block}
.fcol{position:absolute;top:72px;font-size:12px;line-height:2}
.fcol h4{color:var(--white);font-size:17px;font-weight:500;margin-bottom:10px}
.fcol .input{width:220px;height:40px;background:var(--white);color:#999;padding:0 12px;display:flex;align-items:center;margin-top:12px}
.fcol .btn{margin-top:14px;padding:10px 60px}
.copy{position:absolute;bottom:0;left:0;width:1200px;height:52px;border-top:1px solid #333;text-align:center;line-height:52px;font-size:11px}
</style>
</head>
<body>

<div class="abs topbar">
  <div class="contact">
    <span><svg width="12" height="12" viewBox="0 0 24 24"><path fill="#e3151c" d="M6.6 10.8a15 15 0 0 0 6.6 6.6l2.2-2.2c.3-.3.7-.4 1-.2 1.1.4 2.3.6 3.6.6.6 0 1 .4 1 1V20c0 .6-.4 1-1 1A17 17 0 0 1 3 4c0-.6.4-1 1-1h3.5c.6 0 1 .4 1 1 0 1.3.2 2.5.6 3.6.1.3 0 .7-.2 1z"/></svg>+1-555-014-2290</span>
    <span><svg width="12" height="12" viewBox="0 0 24 24"><path fill="#e3151c" d="M2 5h20v14H2zm2 2v.5l8 5 8-5V7z"/></svg>info@talvoro.net</span>
  </div>
  <div class="social"><i class="dot"></i><i class="dot"></i><i class="dot"></i><i class="dot"></i></div>
</div>

<header class="abs header">
  <div class="brand"><i></i>Talvoro Network</div>
  <nav class="nav">
    <a class="active">Home</a><a>Jobs</a><a>Candidates</a><a>Employers</a><a>Pages</a><a>Contact Us</a>
  </nav>
</header>

<section class="abs hero" role="img" aria-label="Photo of a professional working at a laptop in an office">
  <div class="hero-shade"></div>
  <h1>TALVORO NETWORK</h1>
  <p class="sub">Lorem ipsum dolor sit amet, consectetur adipiscing elit, sed do eiusmod tempor incididunt</p>
  <div class="search">
    <div class="field">Keywords</div>
    <div class="field">Salary</div>
    <div class="field">Location</div>
    <div class="go">SEARCH</div>
  </div>
  <div class="trending">
    <b>Trending Keyword :</b><span>jobs</span><span>designer</span><span>developer</span><span>web</span><span>Senior</span>
    <span class="adv"><i class="dot" style="width:10px;height:10px"></i>Advanced Search</span>
  </div>
  <div class="cats">
    <div class="cat"><svg viewBox="0 0 52 52" fill="none" stroke="#fff" stroke-width="2"><circle cx="26" cy="26" r="22"/><path d="M16 34l8-8 5 5 9-11"/></svg>Sales &amp; Marketing</div>
    <div class="cat"><svg viewBox="0 0 52 52" fill="none" stroke="#fff" stroke-width="2"><circle cx="26" cy="26" r="22"/><circle cx="26" cy="26" r="10"/></svg>Restaurant</div>
    <div class="cat"><svg viewBox="0 0 52 52" fill="none" stroke="#fff" stroke-width="2"><rect x="10" y="12" width="32" height="22" rx="2"/><path d="M6 40h40"/></svg>IT &amp; Computer</div>
    <div class="cat"><svg viewBox="0 0 52 52" fill="none" stroke="#fff" stroke-width="2"><rect x="8" y="14" width="36" height="24" rx="2"/><path d="M8 22h36"/></svg>Financial Services</div>
    <div class="cat"><svg viewBox="0 0 52 52" fill="none" stroke="#fff" stroke-width="2"><path d="M8 40h36M12 40V24M22 40V16M32 40V20M42 40V12"/></svg>Finance &amp; Business</div>
    <div class="cat"><svg viewBox="0 0 52 52" fill="none" stroke="#fff" stroke-width="2"><circle cx="26" cy="18" r="8"/><path d="M12 44c0-8 6-14 14-14s14 6 14 14"/></svg>Engineering</div>
  </div>
</section>

<h2 class="abs section-title" style="top:828px">Find The Right job.Right Now.</h2>
<p class="abs section-sub" style="top:878px">Lorem ipsum dolor sit amet, consectetur adipiscing elit, sed do eiusmod tempor incididunt ut labore et dolore magna aliqua</p>

<div class="abs tabs"><span class="tab on">Features Jobs</span><span class="tab">Recommended Jobs</span></div>

<div class="abs jobs">
  <div class="job"><i class="flag"></i><div class="co">Lumriva</div><div class="info"><h4>Lorem ipsum dolor sit amet</h4><p><i></i>Company</p><p><i></i>Sed ut perspiciatis unde</p><p><i></i>1 days ago</p></div><span class="type">Full Time</span><svg class="heart" viewBox="0 0 24 24"><path fill="none" stroke="#999" stroke-width="2" d="M12 20s-7-4.5-7-10a4 4 0 0 1 7-2.6A4 4 0 0 1 19 10c0 5.5-7 10-7 10z"/></svg></div>
  <div class="job"><i class="flag"></i><div class="co">Lumriva</div><div class="info"><h4>Lorem ipsum dolor sit amet</h4><p><i></i>Company</p><p><i></i>Sed ut perspiciatis unde</p><p><i></i>1 days ago</p></div><span class="type">Full Time</span><svg class="heart" viewBox="0 0 24 24"><path fill="none" stroke="#999" stroke-width="2" d="M12 20s-7-4.5-7-10a4 4 0 0 1 7-2.6A4 4 0 0 1 19 10c0 5.5-7 10-7 10z"/></svg></div>
  <div class="job"><i class="flag"></i><div class="co">Ostrivo</div><div class="info"><h4>Lorem ipsum dolor sit amet</h4><p><i></i>Company</p><p><i></i>Sed ut perspiciatis unde</p><p><i></i>1 days ago</p></div><span class="type">Freelance</span><svg class="heart" viewBox="0 0 24 24"><path fill="none" stroke="#999" stroke-width="2" d="M12 20s-7-4.5-7-10a4 4 0 0 1 7-2.6A4 4 0 0 1 19 10c0 5.5-7 10-7 10z"/></svg></div>
  <div class="job"><i class="flag"></i><div class="co">Kelmora</div><div class="info"><h4>Lorem ipsum dolor sit amet</h4><p><i></i>Company</p><p><i></i>Sed ut perspiciatis unde</p><p><i></i>1 days ago</p></div><span class="type">Part Time</span><svg class="heart" viewBox="0 0 24 24"><path fill="none" stroke="#999" stroke-width="2" d="M12 20s-7-4.5-7-10a4 4 0 0 1 7-2.6A4 4 0 0 1 19 10c0 5.5-7 10-7 10z"/></svg></div>
  <div class="job"><i class="flag"></i><div class="co">Parvenne</div><div class="info"><h4>Lorem ipsum dolor sit amet</h4><p><i></i>Company</p><p><i></i>Sed ut perspiciatis unde</p><p><i></i>1 days ago</p></div><span class="type">Full Time</span><svg class="heart" viewBox="0 0 24 24"><path fill="none" stroke="#999" stroke-width="2" d="M12 20s-7-4.5-7-10a4 4 0 0 1 7-2.6A4 4 0 0 1 19 10c0 5.5-7 10-7 10z"/></svg></div>
  <div class="job"><i class="flag"></i><div class="co">Lumriva</div><div class="info"><h4>Lorem ipsum dolor sit amet</h4><p><i></i>Company</p><p><i></i>Sed ut perspiciatis unde</p><p><i></i>1 days ago</p></div><span class="type">Full Time</span><svg class="heart" viewBox="0 0 24 24"><path fill="none" stroke="#999" stroke-width="2" d="M12 20s-7-4.5-7-10a4 4 0 0 1 7-2.6A4 4 0 0 1 19 10c0 5.5-7 10-7 10z"/></svg></div>
</div>

<div class="abs" style="top:1630px;left:0;width:1200px;text-align:center"><span class="btn">Browse All Jobs</span></div>

<section class="abs companies">
  <p class="label">FEATURED COMPANIES</p>
  <h2>Compose the perfect website. No design experience necessary</h2>
  <div class="co-cards">
    <div class="co-card"><div class="photo" role="img" aria-label="Photo of colleagues in a meeting room"></div><i class="badge"></i><h3>Ostrivo</h3><div class="stars">★★★★☆</div><p class="meta">Sed ut perspiciatis unde omnis iste natus</p><p class="meta">+1 555 010 4471</p></div>
    <div class="co-card"><div class="photo" role="img" aria-label="Photo of a team working together at a desk"></div><i class="badge red"></i><h3>Parvenne</h3><div class="stars">★★★★☆</div><p class="meta">Sed ut perspiciatis unde omnis iste natus</p><p class="meta">+1 555 010 4472</p></div>
    <div class="co-card"><div class="photo" role="img" aria-label="Photo of hands typing on a laptop"></div><i class="badge"></i><h3>Kelmora</h3><div class="stars">★★★★☆</div><p class="meta">Sed ut perspiciatis unde omnis iste natus</p><p class="meta">+1 555 010 4473</p></div>
  </div>
  <div class="pager"><i></i><i></i><i></i></div>
</section>

<h2 class="abs section-title" style="top:2624px">What makes us special</h2>
<div class="abs features">
  <div class="feature"><h4><i></i>Free and Paid Membership</h4><p>Sed ut perspiciatis unde omnis iste natus error sit voluptatem accusantium doloremque laudantium.</p><p class="more">READ MORE ›</p></div>
  <div class="feature"><h4><i></i>Build resume Online</h4><p>Sed ut perspiciatis unde omnis iste natus error sit voluptatem accusantium doloremque laudantium.</p><p class="more">READ MORE ›</p></div>
  <div class="feature"><h4><i></i>Job Suggestions</h4><p>Sed ut perspiciatis unde omnis iste natus error sit voluptatem accusantium doloremque laudantium.</p><p class="more">READ MORE ›</p></div>
</div>

<div class="abs" style="top:3016px;left:0;width:1200px;text-align:center"><span class="stars" style="color:#f4b400">★★★★★</span></div>
<p class="abs quote">Sed ut perspiciatis unde omnis iste natus error sit voluptatem accusantium doloremque laudantium, totam rem aperiam, eaque ipsa quae ab illo inventore veritatis et quasi architecto beatae vitae dicta sunt explicabo</p>
<div class="abs avatars">
  <div class="avatar" role="img" aria-label="Client portrait"></div>
  <div class="avatar big" role="img" aria-label="Client portrait"></div>
  <div class="avatar" role="img" aria-label="Client portrait"></div>
</div>
<p class="abs" style="top:3300px;left:0;width:1200px;text-align:center;color:var(--red);font-weight:600;font-size:14px">Mara Quill</p>
<p class="abs" style="top:3322px;left:0;width:1200px;text-align:center;color:var(--grey);font-size:11px">Web developer</p>

<section class="abs stats">
  <div class="stat"><div class="ring"><svg viewBox="0 0 46 46" fill="none" stroke="#fff" stroke-width="2"><rect x="10" y="6" width="26" height="34" rx="2"/><path d="M16 16h14M16 24h14M16 32h8"/></svg></div><b>890+</b><span>Jobs Available</span></div>
  <div class="stat"><div class="ring"><svg viewBox="0 0 46 46" fill="none" stroke="#fff" stroke-width="2"><path d="M8 36h30M12 36V22M22 36V14M32 36V18"/></svg></div><b>7485+</b><span>Active Resumes</span></div>
  <div class="stat"><div class="ring"><svg viewBox="0 0 46 46" fill="none" stroke="#fff" stroke-width="2"><circle cx="23" cy="16" r="8"/><path d="M9 40c0-8 6-14 14-14s14 6 14 14"/></svg></div><b>785+</b><span>Employer Profiles</span></div>
  <div class="stat"><div class="ring"><svg viewBox="0 0 46 46" fill="none" stroke="#fff" stroke-width="2"><path d="M6 24l8-8 9 6 9-6 8 8-11 11-6-5-6 5z"/></svg></div><b>542+</b><span>Positions Matched</span></div>
</section>

<h2 class="abs section-title" style="top:3924px">Featured Candidate</h2>
<p class="abs section-sub" style="top:3974px">Lorem ipsum dolor sit amet, consectetur adipiscing elit, sed do eiusmod tempor incididunt ut labore et dolore magna aliqua</p>
<div class="abs grid">
  <div class="cand"><div class="pic" role="img" aria-label="Candidate portrait"></div><h4>SED UT PERSPICIATIS</h4><span>Lorem ipsum</span></div>
  <div class="cand"><div class="pic" role="img" aria-label="Candidate portrait"></div><h4>LOREM IPSUM</h4><span>Lorem ipsum</span></div>
  <div class="cand"><div class="pic" role="img" aria-label="Candidate portrait"></div><h4>SED UT PERSPICIATIS</h4><span>Lorem ipsum</span></div>
  <div class="cand"><div class="pic" role="img" aria-label="Candidate portrait"></div><h4>LOREM IPSUM</h4><span>Lorem ipsum</span></div>
  <div class="cand"><div class="pic" role="img" aria-label="Candidate portrait"></div><h4>LOREM IPSUM</h4><span>Lorem ipsum</span></div>
  <div class="cand"><div class="pic" role="img" aria-label="Candidate portrait"></div><h4>SED UT PERSPICIATIS</h4><span>Lorem ipsum</span></div>
  <div class="cand"><div class="pic" role="img" aria-label="Candidate portrait"></div><h4>LOREM IPSUM</h4><span>Lorem ipsum</span></div>
  <div class="cand"><div class="pic" role="img" aria-label="Candidate portrait"></div><h4>SED UT PERSPICIATIS</h4><span>Lorem ipsum</span></div>
</div>
<div class="abs" style="top:4632px;left:0;width:1200px;text-align:center"><span class="btn" style="border-radius:22px">All Candidates</span></div>

<footer class="abs footer">
  <div class="about">Lorem ipsum dolor sit amet, consectetur adipiscing elit, sed do eiusmod tempor incididunt ut labore et dolore magna aliqua. Ut enim ad minim veniam, quis nostrud exercitation ullamco laboris.<br><span class="outline">Learn more</span>
    <div class="fsocial"><i></i><i></i><i></i><i></i></div>
  </div>
  <div class="fcol" style="left:470px"><h4>For Candidate</h4>Browse Jobs<br>All Categories<br>Companies<br>My Account</div>
  <div class="fcol" style="left:676px"><h4>For Employers</h4>All Resumes<br>All Categories<br>My Jobs<br>My Account</div>
  <div class="fcol" style="left:872px"><h4>For Candidate</h4>Sed ut perspiciatis unde<br>iste natus error sit
    <div class="input">Enter Your Email Address</div><span class="btn">Subscribe</span></div>
  <div class="copy">© 2024 Talvoro Network. All Rights Reserved.</div>
</footer>

</body>
</html>
```